Brightway Haul & Upkeep Services, are a company that offers a 'one stop shop' pre-move clean up a

I have already selected a logo which I would like on the front of the business cards along with phone numbers, web address and email which are:
0487650392
www.brightwayhaul.com.au
brightwayhaulandupkeep@mailbox.example

On the back of the card I would like to list some of the types of service we offer (clean - move - repairs/maintenance) which are:
CLEAN - windows, gutters, solar panels, driveways/paths, carpets.
MOVE - Small/medium size house/office moves, large item pick-up & delivery, yard clean-up and removal.
General maintenance and repairs.

I would like the blue logo on a gray background.

Thanks

```html
<!DOCTYPE html>
<html lang="en">
<head>
<meta charset="utf-8">
<title>Brightway Haul &amp; Upkeep Services – Business Cards</title>
<link rel="stylesheet" href="https://fonts.googleapis.com/css2?family=Open+Sans:wght@400;600;700;800&display=swap">
<style>
  :root {
    --page-bg: #ece9e6;
    --card-light: #f4f4f5;
    --card-mid: #cfd0d2;
    --brand-blue: #2f7fc6;
    --brand-dark: #1c1c1e;
    --text-dark: #2a2a2c;
    --band-black: #0b0b0c;
  }
  * { box-sizing: border-box; margin: 0; padding: 0; }
  html, body { width: 1200px; height: 790px; overflow: hidden; }
  body {
    background: var(--page-bg);
    font-family: "Open Sans", Arial, sans-serif;
    position: relative;
  }
  .card {
    position: absolute;
    width: 560px;
    height: 320px;
    overflow: hidden;
    box-shadow: 0 6px 18px rgba(0,0,0,0.18);
  }

  /* Front card */
  .card-front {
    left: 30px; top: 90px;
    background: linear-gradient(120deg, var(--card-light) 0%, var(--card-mid) 60%, #b9babd 100%);
  }
  .front-bands { position: absolute; left: 0; bottom: 0; width: 560px; height: 90px; }
  .front-brand {
    position: absolute; left: 40px; top: 130px;
    display: flex; align-items: center; gap: 9px;
  }
  .brand-square {
    width: 20px; height: 20px; background: var(--brand-blue); flex: none;
  }
  .front-brand .brand-name {
    font-weight: 800; color: var(--brand-blue);
    font-size: 17px; line-height: 1.15; text-transform: uppercase;
  }
  .contact-list {
    position: absolute; left: 272px; top: 100px;
    list-style: none;
  }
  .contact-item {
    display: flex; align-items: center; gap: 8px;
    font-size: 11.5px; color: var(--text-dark); margin-bottom: 12px;
    white-space: nowrap;
  }
  .contact-item.phone { font-size: 14px; }
  .contact-icon { width: 13px; height: 13px; flex: none; }

  /* Back card */
  .card-back {
    left: 610px; top: 390px;
    background: linear-gradient(120deg, #f6f6f7 0%, #dcdddf 70%, #cbccce 100%);
  }
  .back-brand {
    position: absolute; left: 0; right: 0; top: 56px;
    display: flex; align-items: center; justify-content: center; gap: 14px;
  }
  .back-brand .brand-square { width: 34px; height: 34px; }
  .back-brand .brand-name {
    font-weight: 800; color: var(--brand-blue);
    font-size: 36px; line-height: 1.05; text-transform: uppercase;
  }
  .back-tagline {
    position: absolute; left: 0; right: 0; top: 110px; text-align: center;
    font-weight: 700; font-size: 21px; color: var(--brand-dark); text-transform: uppercase;
  }
  .services-heading {
    position: absolute; left: 0; right: 0; top: 156px; text-align: center;
    font-weight: 700; font-size: 19px; letter-spacing: 7px; color: var(--brand-blue);
  }
  .services-list {
    position: absolute; left: 0; right: 0; top: 196px; text-align: center;
    list-style: none; font-size: 17px; font-weight: 600; color: var(--text-dark);
    text-transform: uppercase; line-height: 1.55;
  }
</style>
</head>
<body>

<section class="card card-front" aria-label="Business card front">
  <svg class="front-bands" viewBox="0 0 560 90" aria-hidden="true">
    <polygon points="0,66 290,66 290,90 0,90" fill="var(--brand-blue)"/>
    <polygon points="300,34 560,0 560,90 280,90" fill="var(--band-black)"/>
    <polygon points="0,63 290,63 288,66 0,66" fill="#ffffff" opacity="0.6"/>
  </svg>

  <div class="front-brand">
    <span class="brand-square" aria-hidden="true"></span>
    <span class="brand-name">Brightway Haul<br>&amp; Upkeep Services</span>
  </div>

  <ul class="contact-list">
    <li class="contact-item phone">
      <svg class="contact-icon" viewBox="0 0 16 16" aria-hidden="true">
        <circle cx="8" cy="8" r="7.5" fill="none" stroke="var(--brand-blue)" stroke-width="1.2"/>
        <path d="M5.5 4.2 L7 4 L7.6 6 L6.7 6.8 Q7.4 8.6 9.2 9.3 L10 8.4 L12 9 L11.8 10.5 Q8 11.5 5.5 4.2 Z" fill="var(--brand-blue)"/>
      </svg>
      0487650392
    </li>
    <li class="contact-item">
      <svg class="contact-icon" viewBox="0 0 16 16" aria-hidden="true">
        <circle cx="8" cy="8" r="7.5" fill="var(--brand-blue)"/>
        <rect x="4" y="5.2" width="8" height="5.6" fill="#fff"/>
        <path d="M4 5.2 L8 8.4 L12 5.2" fill="none" stroke="var(--brand-blue)" stroke-width="0.9"/>
      </svg>
      brightwayhaulandupkeep@mailbox.example
    </li>
    <li class="contact-item">
      <svg class="contact-icon" viewBox="0 0 16 16" aria-hidden="true">
        <circle cx="8" cy="8" r="7" fill="none" stroke="var(--brand-blue)" stroke-width="1.3"/>
        <ellipse cx="8" cy="8" rx="3" ry="7" fill="none" stroke="var(--brand-blue)" stroke-width="1"/>
        <line x1="1" y1="8" x2="15" y2="8" stroke="var(--brand-blue)" stroke-width="1"/>
      </svg>
      www.brightwayhaul.com.au
    </li>
  </ul>
</section>

<section class="card card-back" aria-label="Business card back">
  <div class="back-brand">
    <span class="brand-square" aria-hidden="true"></span>
    <span class="brand-name">Brightway Haul</span>
  </div>
  <p class="back-tagline">&amp; Upkeep Services</p>
  <p class="services-heading">Services we offer</p>
  <ul class="services-list">
    <li>• Clean • Move</li>
    <li>• General maintenance and repairs.</li>
  </ul>
</section>

</body>
</html>
```